Tollin Waste Website Design

Our new start-up needs a website design. We plan to help businesses find more sustainable ways to manage their waste. Our initial website aims to gather contact data from potential business customers and comprehensive information from waste facilities and waste transporters. We have a logo design (attached) which we would like included in the website design. I have also attached a number of pages that describe what information should appear on each page as well as a web design brief file that describes the look we are after.

```html
<!DOCTYPE html>
<html lang="en">
<head>
<meta charset="utf-8">
<title>Tollin Waste</title>
<link href="https://fonts.googleapis.com/css2?family=Lato:wght@400;700;900&display=swap" rel="stylesheet">
<style>
  :root {
    --white: #ffffff;
    --hero-dark: #2b2d2c;
    --hero-mid: #4a4f4b;
    --hero-blue: #2f4a6b;
    --hero-green: #55663e;
    --footer-bg: rgba(22, 24, 24, 0.92);
    --btn-top: #97c93a;
    --btn-bottom: #5a9a24;
    --brand-green: #8cc63f;
    --text-soft: #e6e6e6;
  }
  * { margin: 0; padding: 0; box-sizing: border-box; }
  html, body { width: 1200px; height: 738px; overflow: hidden; }
  body { font-family: "Lato", sans-serif; color: var(--white); background: var(--hero-dark); }

  .page { position: relative; width: 1200px; height: 738px; overflow: hidden; }

  .hero-photo {
    position: absolute; inset: 0;
    background:
      radial-gradient(ellipse at 55% 45%, rgba(120,130,110,0.35), transparent 55%),
      linear-gradient(120deg, var(--hero-mid) 0%, var(--hero-dark) 35%, var(--hero-green) 55%, var(--hero-dark) 72%, var(--hero-blue) 100%);
  }
  .hero-photo::after { content: ""; position: absolute; inset: 0; background: rgba(0,0,0,0.35); }

  .site-header {
    position: absolute; top: 32px; left: 74px; right: 74px;
    display: flex; justify-content: space-between; align-items: center;
  }
  .brand { display: flex; align-items: center; gap: 10px; }
  .brand-dot { width: 62px; height: 62px; border-radius: 50%; border: 4px solid var(--white); }
  .brand-name { font-size: 30px; font-weight: 700; line-height: 1; letter-spacing: 1px; text-transform: uppercase; }

  .main-nav { display: flex; gap: 34px; margin-top: -8px; }
  .main-nav a { color: var(--white); text-decoration: none; font-size: 13px; text-transform: uppercase; }

  .hero-content { position: absolute; top: 270px; left: 0; right: 0; text-align: center; }
  .hero-title { font-size: 45px; font-weight: 900; line-height: 1.05; text-transform: uppercase; letter-spacing: 0.5px; }
  .hero-subtitle { font-size: 31px; font-weight: 700; margin-top: 2px; }

  .audience-links { display: flex; justify-content: center; gap: 14px; margin-top: 34px; }
  .audience-btn {
    width: 284px; height: 76px; display: flex; align-items: center; justify-content: center;
    border: 2px solid var(--white); border-radius: 10px;
    background: linear-gradient(var(--btn-top), var(--btn-bottom));
    color: var(--white); text-decoration: none; font-size: 24px; font-weight: 700;
  }

  .site-footer {
    position: absolute; left: 0; right: 0; bottom: 0; height: 67px;
    background: var(--footer-bg);
    display: flex; align-items: center; justify-content: space-between;
    padding: 0 88px 0 75px;
  }
  .copyright { font-size: 12px; color: var(--text-soft); margin-top: 6px; }
  .footer-mark {
    position: absolute; left: 570px; top: -30px; width: 60px; height: 60px;
    border-radius: 50%; background: var(--white); border: 4px solid var(--brand-green);
  }
  .social-links { display: flex; gap: 22px; margin-top: 4px; }
  .social-links span { width: 20px; height: 20px; border-radius: 50%; background: var(--text-soft); display: block; }
</style>
</head>
<body>
<div class="page">
  <div class="hero-photo" role="img" aria-label="Photo of a worker in safety gear sorting glass on a recycling plant conveyor"></div>

  <header class="site-header">
    <div class="brand">
      <span class="brand-dot"></span>
      <span class="brand-name">Tollin Waste</span>
    </div>
    <nav class="main-nav">
      <a href="#">About us</a>
      <a href="#">What we do</a>
      <a href="#">Resources</a>
      <a href="#">Contact us</a>
    </nav>
  </header>

  <section class="hero-content">
    <h1 class="hero-title">Welcome to Tollin Waste</h1>
    <p class="hero-subtitle">Take control of your waste here</p>
    <div class="audience-links">
      <a class="audience-btn" href="#">Waste Producers</a>
      <a class="audience-btn" href="#">Waste Facilities</a>
      <a class="audience-btn" href="#">Waste Transporters</a>
    </div>
  </section>

  <footer class="site-footer">
    <p class="copyright">Copyright © 2018 Company&nbsp; Name All rights Reserved</p>
    <span class="footer-mark" aria-hidden="true"></span>
    <div class="social-links">
      <span aria-label="Social link"></span>
      <span aria-label="Social link"></span>
      <span aria-label="Social link"></span>
      <span aria-label="Social link"></span>
      <span aria-label="Social link"></span>
    </div>
  </footer>
</div>
</body>
</html>
```